business card deign

Logo needs the following on it.
1. attached logo
2. Tagline - "If it keeps a drink cold or the party going...we do it!"
3. Name- Dalton Pikes, Founder and CPO
4. Address - 412 E. Carver Avenue, Ste 2207, Tampa, FL. 33917
5. Phone - 555.318.4726

```html
<!DOCTYPE html>
<html lang="en">
<head>
<meta charset="utf-8">
<title>Talloway Business Card</title>
<link href="https://fonts.googleapis.com/css2?family=Montserrat:wght@300;400;600;700&display=swap" rel="stylesheet">
<style>
  :root {
    --backdrop: #1c1c1f;
    --card-black: #0b0b0c;
    --card-white: #ffffff;
    --ink: #111111;
    --ink-soft: #6f6f6f;
    --foil: #c9c9cc;
    --band: #0b0b0c;
    --band-text: #ffffff;
  }
  * { box-sizing: border-box; margin: 0; padding: 0; }
  html, body {
    width: 1200px; height: 800px; overflow: hidden;
    background: var(--backdrop);
    font-family: "Montserrat", sans-serif;
  }
  .stage {
    width: 1200px; height: 800px;
    display: flex; align-items: center; justify-content: center; gap: 40px;
  }
  .card {
    width: 540px; height: 309px; border-radius: 22px; overflow: hidden;
    position: relative;
    box-shadow: 0 18px 40px rgba(0,0,0,.45);
  }
  /* Front */
  .card-front {
    background: var(--card-black);
    display: flex; align-items: center; justify-content: center;
  }
  .brand-front {
    color: var(--foil); font-weight: 700; font-size: 44px; letter-spacing: 14px;
    text-transform: uppercase; padding-left: 14px;
  }
  /* Back */
  .card-back {
    background: var(--card-white); color: var(--ink);
    display: grid; grid-template-rows: 1fr 46px;
  }
  .back-body {
    display: grid; grid-template-columns: 210px 1px 1fr; align-items: center;
    padding: 0 28px 0 22px;
  }
  .brand-back {
    font-weight: 700; font-size: 26px; letter-spacing: 8px; text-transform: uppercase;
    text-align: center;
  }
  .divider { width: 1px; height: 150px; background: var(--ink); }
  .details { padding-left: 26px; }
  .person-name { font-weight: 700; font-size: 19px; text-transform: uppercase; letter-spacing: .5px; }
  .person-role { font-weight: 400; font-size: 16px; color: var(--ink-soft); margin-bottom: 14px; }
  .address, .contact-line {
    font-weight: 300; font-size: 14px; color: var(--ink-soft); line-height: 1.45;
  }
  .address { margin-bottom: 6px; }
  .contact-line { display: flex; align-items: center; gap: 8px; }
  .contact-line svg { width: 14px; height: 14px; fill: var(--ink); flex: none; }
  .tagline-band {
    background: var(--band); color: var(--band-text);
    display: flex; align-items: center; justify-content: center;
    font-weight: 600; font-size: 14px; letter-spacing: .3px;
  }
</style>
</head>
<body>
<main class="stage">
  <section class="card card-front" aria-label="Card front">
    <span class="brand-front">Talloway</span>
  </section>

  <section class="card card-back" aria-label="Card back">
    <div class="back-body">
      <div class="brand-back">Talloway</div>
      <div class="divider"></div>
      <div class="details">
        <p class="person-name">Dalton Pikes</p>
        <p class="person-role">Founder and CPO</p>
        <p class="address">412 E. Carver Avenue,<br>Ste 2207, Tampa, FL. 33917</p>
        <p class="contact-line">
          <svg viewBox="0 0 24 24" aria-hidden="true"><path d="M6.6 10.8a15.1 15.1 0 0 0 6.6 6.6l2.2-2.2c.3-.3.7-.4 1-.2 1.1.4 2.3.6 3.6.6.6 0 1 .4 1 1V20c0 .6-.4 1-1 1C10.6 21 3 13.4 3 4c0-.6.4-1 1-1h3.5c.6 0 1 .4 1 1 0 1.3.2 2.5.6 3.6.1.3 0 .7-.2 1l-2.3 2.2z"/></svg>
          555.318.4726
        </p>
        <p class="contact-line">
          <svg viewBox="0 0 24 24" aria-hidden="true"><path d="M2 5h20v14H2V5zm2 2v.5l8 5 8-5V7H4zm16 2.8-8 5-8-5V17h16V9.8z"/></svg>
          info@talloway.com
        </p>
      </div>
    </div>
    <div class="tagline-band">If it keeps a drink cold or the party going...we do it!</div>
  </section>
</main>
</body>
</html>
```